I want a creative, filmic, folk, jazz take on me performing on stage on an old Broadway Theatre; the point of view is that of a spectator from the balcony of the theatre. Includes the title of the project: Regrettably The Lanterns Have Dimmed Before Our Walk Home; and my name on it: Tobin Varelka. Let’s include iconic people in the audience from that era: 60’s/70’s like Rex Pomfrey, Vera Lanshaw, Harriet Quibble, Greta Voss, Otis Crandell, Lionel Vashetti, Walter Bixanti, Ignatius Pell Ravenna, Curtis Fellowes, Oren Thale, Hobart Grise, Clement Aubrich, Tullio Varsenta, Minna Quell, Lonnie Farrow Jr, Winifred Holm, Percy Tamble, Rosalind Vane, Hugh Pettigrew, Dusty, Norris Feldlake, Glenn Marchbank, Roy Quentell, Ida Broughton, Virgil Oakhampton

```html
<!DOCTYPE html>
<html lang="en">
<head>
<meta charset="utf-8">
<title>Tobin Varelka / Regrettably The Lanterns Have Dimmed Before Our Walk Home</title>
<link rel="stylesheet" href="https://fonts.googleapis.com/css2?family=Libre+Caslon+Text:wght@400&display=swap">
<style>
  :root {
    --frame-red: #b4463b;
    --panel-cream: #f1eae0;
    --title-brown: #5b4740;
    --header-cream: #f4e6d6;
    --wall-beige: #e3cf9f;
    --wall-slate: #a3aa9c;
    --wall-charcoal: #56504c;
    --wall-orange: #e37e1c;
    --wall-red: #c33a2c;
    --wall-mustard: #c9a321;
  }
  html, body {
    margin: 0;
    padding: 0;
    width: 1200px;
    height: 1200px;
    overflow: hidden;
    background: #ffffff;
  }
  .cover {
    position: relative;
    width: 1200px;
    height: 1200px;
    background: var(--frame-red);
    font-family: "Libre Caslon Text", Georgia, serif;
  }
  .cover-header {
    position: absolute;
    left: 42px;
    top: 56px;
    width: 1128px;
    margin: 0;
    font-size: 24.5px;
    font-weight: 400;
    line-height: 1;
    color: var(--header-cream);
    white-space: nowrap;
    letter-spacing: -0.2px;
  }
  .cover-panel {
    position: absolute;
    left: 32px;
    top: 101px;
    width: 1135px;
    height: 1066px;
    background: var(--panel-cream);
  }
  .stage-photo {
    position: absolute;
    left: 10px;
    top: 13px;
    width: 838px;
    height: 1043px;
    background:
      linear-gradient(180deg,
        var(--wall-beige) 0%,
        var(--wall-beige) 9%,
        var(--wall-slate) 16%,
        var(--wall-charcoal) 28%,
        var(--wall-slate) 38%,
        var(--wall-orange) 46%,
        var(--wall-slate) 55%,
        var(--wall-charcoal) 65%,
        var(--wall-red) 72%,
        var(--wall-charcoal) 80%,
        var(--wall-mustard) 86%,
        var(--wall-mustard) 100%);
  }
  .cover-title {
    position: absolute;
    left: 868px;
    top: 110px;
    height: 906px;
    margin: 0;
    writing-mode: vertical-rl;
    transform: rotate(180deg);
    font-size: 58px;
    font-weight: 400;
    line-height: 62px;
    color: var(--title-brown);
    text-shadow: 1px 1px 2px rgba(40, 25, 20, 0.35);
    white-space: nowrap;
  }
  .cover-title .artist-line {
    display: block;
  }
  .cover-title .title-line {
    display: block;
    text-transform: uppercase;
  }
</style>
</head>
<body>
  <main class="cover">
    <p class="cover-header">Tobin Varelka / REGRETTABLY THE LANTERNS HAVE DIMMED BEFORE OUR WALK HOME</p>
    <section class="cover-panel">
      <div class="stage-photo" role="img" aria-label="Photo of the singer performing with an acoustic guitar at a microphone, eyes covered with tape, in front of a wall painted in beige, slate, charcoal, orange, red and mustard blocks"></div>
      <h1 class="cover-title">
        <span class="artist-line">Tobin Varelka /</span>
        <span class="title-line">Regrettably the lanterns</span>
        <span class="title-line">have dimmed before</span>
        <span class="title-line">our walk home</span>
      </h1>
    </section>
  </main>
</body>
</html>
```